Lumora Systems New Website - IT Infrastructure | Smart Cabinet | Micro Data Center

We're an IT SI providing Server Room Design & Build | All-in-One Rack & Smart Cabinet | Structured Cabling | IT Relocation | Maintenance. Old website can be found at www.lumorasys.com.hk. We'd like a brand new wix website which is modern, minimalist, interactive with some animation. Website content will be mostly static and include our service, our project, news and events, about us, contacts, blogs, partners and brands, etc.

reference sites:
We'd like to see more designs referring to below

https://www.pixelvane.example/design/41736205
https://www.pixelvane.example/design/41892417
https://velbrinn.example/

Animation (scrolling effect) referring to
https://velbrinn.example/intelligence/smart-office-room/
Updates

we'd like below style.

Designs look the same

Target Market(s)

Commercials in HK

Industry/Entity Type

IT, Technology, Data Center

Coding

Coded - Design and coding required

Font styles to use
Sans Serif

Requirements
Must have
• CMS, Some Interactive Elements/ Graphics

```html
<!DOCTYPE html>
<html lang="en">
<head>
<meta charset="utf-8">
<title>Lumora Systems – IT Infrastructure</title>
<link rel="stylesheet" href="https://fonts.googleapis.com/css2?family=Ubuntu:wght@500;700&family=Lato:wght@400;700&display=swap">
<style>
:root{
  --navy:#14204a;
  --navy-deep:#0f1a3c;
  --red:#d9301f;
  --ink:#1b1b1b;
  --muted:#6b6b6b;
  --grey:#e6e6e6;
  --white:#ffffff;
  --black:#141414;
}
*{box-sizing:border-box;margin:0;padding:0}
html,body{width:1200px;height:4959px;overflow:hidden}
body{position:relative;font-family:'Lato',sans-serif;color:var(--ink);background:var(--white)}
.abs{position:absolute}
h1,h2,h3,h4{font-family:'Ubuntu',sans-serif;font-weight:700}
.section-title{position:absolute;left:0;width:1200px;text-align:center;font-size:40px}
.section-title::after{content:"";display:block;width:104px;height:4px;background:var(--red);margin:12px auto 0}
.btn{position:absolute;background:var(--red);color:var(--white);font-family:'Ubuntu',sans-serif;font-weight:500;font-size:17px;display:flex;align-items:center;justify-content:center;border-radius:0 12px 12px 0}
.ph{position:absolute}

/* header / hero */
.hero{left:0;top:0;width:1200px;height:593px;background:var(--navy);}
.hero-photo{left:0;top:0;width:1200px;height:593px;border-radius:0 0 90px 0;background:linear-gradient(120deg,#2a3d66 0%,#5a7299 35%,#3b5277 60%,#1c2a4c 100%)}
.brand{position:absolute;display:flex;align-items:center;gap:8px;color:var(--white);font-family:'Ubuntu',sans-serif;font-weight:500}
.brand .mark{width:22px;height:22px;border:2px solid var(--white)}
.nav{left:375px;top:30px;display:flex;gap:0}
.nav a{color:var(--white);text-decoration:none;font-size:16px;margin-right:42px}
.nav-line{left:0;top:90px;width:1200px;height:1px;background:rgba(255,255,255,.55)}
.nav-dot{left:399px;top:87px;width:8px;height:8px;border-radius:50%;background:var(--red)}
.login{left:973px;top:23px;width:127px;height:40px;font-size:18px}
.play{left:934px;top:284px;width:84px;height:84px;border-radius:50%;background:var(--white);display:flex;align-items:center;justify-content:center}
.play span{width:66px;height:66px;border-radius:50%;background:var(--red);display:flex;align-items:center;justify-content:center}

/* about */
.about{left:0;top:593px;width:1200px;height:703px;background:radial-gradient(ellipse at 30% 60%,#203165 0%,var(--navy) 55%,var(--navy-deep) 100%)}
.about-frame{left:98px;top:135px;width:412px;height:473px;border:5px solid var(--red);border-right:none;border-top:none}
.about-frame::before{content:"";position:absolute;left:-5px;top:0;width:5px;height:100%;background:var(--red)}
.about-frame::after{content:"";position:absolute;right:-5px;bottom:-5px;width:5px;height:30px;background:var(--red)}
.about-photo{left:129px;top:81px;width:441px;height:496px;border-radius:0 0 24px 0;background:linear-gradient(160deg,#8a8f8c 0%,#c59a5a 45%,#6f6a5e 75%,#4d4a44 100%)}
.about-title{left:633px;top:108px;color:var(--white);font-size:42px;line-height:50px}
.about-text{left:636px;top:230px;width:466px;color:#e4e7f0;font-size:14px;line-height:25.8px}
.about-btn{left:637px;top:529px;width:146px;height:41px}

/* services */
.services-title{top:1388px}
.svc{position:absolute;top:1498px;height:273px;background:var(--grey);border-radius:0 0 22px 0;text-align:center}
.svc .img{position:absolute;left:12px;right:12px;top:10px;height:142px}
.svc h3{position:absolute;left:0;right:0;top:170px;font-size:17px;line-height:25px;font-weight:500}
.svc .go{position:absolute;left:50%;top:236px;margin-left:-9px}
.brands{left:98px;top:1843px;width:1004px;height:46px;display:flex;align-items:center;justify-content:space-between}
.arrow-c{width:40px;height:40px;border-radius:50%;background:#e3e3e3;display:flex;align-items:center;justify-content:center}
.brand-name{font-family:'Ubuntu',sans-serif;font-weight:700;font-size:24px;color:#3a3a3a;display:flex;align-items:center;gap:8px}
.brand-name .dot{width:18px;height:18px;border-radius:50%;background:#3a3a3a}

/* projects */
.proj-title{left:100px;top:2038px;font-size:42px}
.proj-text{left:100px;top:2135px;width:360px;font-size:14px;line-height:30px}
.proj{position:absolute;top:2044px;width:273px;height:328px;border-radius:0 0 36px 0;overflow:hidden}
.proj h4{position:absolute;left:20px;bottom:24px;width:240px;color:var(--white);font-size:20px;line-height:29px;font-weight:500}
.proj-next{left:1080px;top:2175px;width:40px;height:40px;background:var(--white);box-shadow:0 2px 6px rgba(0,0,0,.25)}

/* blogs */
.blogs{left:0;top:2458px;width:1200px;height:700px;background:radial-gradient(ellipse at 50% 40%,#22336b 0%,var(--navy) 60%,var(--navy-deep) 100%)}
.blogs .section-title{color:var(--white);top:57px}
.blog{position:absolute;top:2633px;width:322px;height:434px;background:var(--white);border-radius:0 0 36px 0}
.blog .img{position:absolute;left:10px;right:10px;top:8px;height:178px}
.meta{position:absolute;display:flex;align-items:center;gap:10px;font-size:14px}
.meta::before{content:"";width:4px;height:18px;background:var(--red)}
.blog .meta{left:12px;top:203px}
.blog h3{position:absolute;left:12px;top:228px;font-size:25px;font-weight:500}
.blog p{position:absolute;left:12px;top:272px;width:285px;font-size:14px;line-height:21.5px;color:var(--muted)}
.blog .btn{left:12px;top:385px;width:146px;height:40px}

/* news */
.news-title{top:3252px}
.card{position:absolute;background:var(--white);box-shadow:0 2px 12px rgba(0,0,0,.12);border-radius:0 0 26px 0}
.news-big{left:98px;top:3365px;width:476px;height:510px}
.news-big .img{left:10px;top:10px;width:456px;height:206px}
.news-big .meta{left:12px;top:242px}
.news-big h3{position:absolute;left:12px;top:270px;font-size:25px;font-weight:500}
.news-big p{position:absolute;left:12px;top:320px;width:440px;font-size:14px;line-height:21.5px;color:var(--muted)}
.news-big .btn{left:12px;top:440px;width:146px;height:40px}
.news-small{left:599px;width:493px;height:242px}
.news-small .img{left:14px;top:14px;width:196px;height:216px}
.news-small .meta{left:228px;top:22px}
.news-small h3{position:absolute;left:232px;top:56px;width:230px;font-size:21px;line-height:28px;font-weight:500}
.news-small p{position:absolute;left:232px;top:128px;width:245px;font-size:14px;line-height:21.5px;color:var(--muted)}

/* contact */
.contact{left:0;top:3998px;width:1200px;height:540px;background:var(--navy)}
.map{left:560px;top:0;width:640px;height:540px;background:radial-gradient(ellipse at 58% 50%,#7a8aa6 0%,#4a5b82 35%,var(--navy) 72%)}
.contact h2{position:absolute;left:99px;top:95px;color:var(--white);font-size:42px}
.c-row{position:absolute;left:104px;width:408px;color:var(--white);font-size:17px;line-height:32px;display:flex;gap:28px}
.c-row svg{flex:none;margin-top:8px}
.c-line{position:absolute;left:152px;width:360px;height:1px;background:rgba(255,255,255,.6)}

/* footer */
.footer{left:0;top:4537px;width:1200px;height:422px;background:var(--black);color:var(--white)}
.footer h4{position:absolute;top:52px;font-size:18px;font-weight:700;letter-spacing:.5px}
.flinks{position:absolute;top:100px;list-style:none;font-size:16px;line-height:27.5px}
.field{position:absolute;border:1px solid #bbb;border-radius:0 0 10px 0;font-size:9px;font-weight:700;padding:10px 8px;letter-spacing:.4px}
.submit{left:851px;top:306px;width:135px;height:41px;font-size:15px}
.copy{position:absolute;left:102px;top:308px;font-size:15px}
.legal{position:absolute;left:102px;top:350px;font-size:15px}
</style>
</head>
<body>

<!-- Hero -->
<section class="abs hero">
  <div class="ph hero-photo" role="img" aria-label="Engineers reviewing a tablet inside a data center"></div>
  <div class="brand" style="left:99px;top:27px;font-size:20px"><span class="mark"></span>Lumora</div>
  <nav class="abs nav"><a>Home</a><a>About</a><a>Our Services</a><a>Our Projects</a><a>Contact</a></nav>
  <div class="abs nav-line"></div>
  <div class="abs nav-dot"></div>
  <a class="btn login">Login</a>
  <div class="abs play"><span><svg width="22" height="24" viewBox="0 0 22 24"><path d="M3 2 L20 12 L3 22 Z" fill="#fff"/></svg></span></div>
</section>

<!-- About -->
<section class="abs about">
  <div class="abs about-frame"></div>
  <div class="ph about-photo" role="img" aria-label="Miniature workers beside a network cable and connector"></div>
  <h2 class="abs about-title">About<br>Lumora Systems</h2>
  <p class="abs about-text">Lumora Systems is well experienced in delivering the best in Data Center Infrastructure, Network Infrastructure, Structured Cabling, Telephony, Access Control, Video Surveillance, Audiovisual &amp; Conferencing, Relocation &amp; Migration and Maintenance solutions. Our dedication, focus, and expertise wins much recognition of many IT professionals in all industries in the region. In Lumora Systems's Belief, the major reason that we gain a lot of true long-lasting business relationship with our clients was that we offer them the attention, consideration, passion, and professionalism that they deserved.</p>
  <a class="btn about-btn">Read More</a>
</section>

<!-- Services -->
<h2 class="section-title services-title">Our Services</h2>
<div class="svc" style="left:98px;width:245px"><div class="ph img" role="img" aria-label="Engineer with laptop among server racks" style="background:linear-gradient(135deg,#0d2a55,#2d6bb0,#0b1c3a)"></div><h3>Data Center Design<br>And Build</h3><svg class="go" width="18" height="18" viewBox="0 0 18 18"><circle cx="9" cy="9" r="9" fill="var(--red)"/><path d="M5 9h7M9 5.5 12.5 9 9 12.5" stroke="#fff" stroke-width="2" fill="none"/></svg></div>
<div class="svc" style="left:358px;width:237px"><div class="ph img" role="img" aria-label="Close-up of fiber optic cable ends" style="background:radial-gradient(circle at 60% 60%,#c8413a,#3a1520 60%,#120a14)"></div><h3>Structured Cabling And<br>Fiber Backbone</h3><svg class="go" width="18" height="18" viewBox="0 0 18 18"><circle cx="9" cy="9" r="9" fill="var(--red)"/><path d="M5 9h7M9 5.5 12.5 9 9 12.5" stroke="#fff" stroke-width="2" fill="none"/></svg></div>
<div class="svc" style="left:608px;width:239px"><div class="ph img" role="img" aria-label="Patch panel with blue network cables" style="background:linear-gradient(180deg,#2a3e5e,#5a9ad2,#1d2a40)"></div><h3>All-in-one Rack /<br>Micro-data Center</h3><svg class="go" width="18" height="18" viewBox="0 0 18 18"><circle cx="9" cy="9" r="9" fill="var(--red)"/><path d="M5 9h7M9 5.5 12.5 9 9 12.5" stroke="#fff" stroke-width="2" fill="none"/></svg></div>
<div class="svc" style="left:866px;width:235px;height:263px"><div class="ph img" role="img" aria-label="Modern conference room with long table" style="background:linear-gradient(180deg,#2a3436,#6b7a78,#1d2325)"></div><h3>Audiovisual And<br>Conference Room</h3><svg class="go" width="18" height="18" viewBox="0 0 18 18"><circle cx="9" cy="9" r="9" fill="var(--red)"/><path d="M5 9h7M9 5.5 12.5 9 9 12.5" stroke="#fff" stroke-width="2" fill="none"/></svg></div>

<div class="abs brands">
  <span class="arrow-c"><svg width="10" height="14"><path d="M8 2 3 7l5 5" stroke="#333" stroke-width="2" fill="none"/></svg></span>
  <span class="brand-name"><span class="dot"></span>Corvane</span>
  <span class="brand-name">Haldenor</span>
  <span class="brand-name">Trivex</span>
  <span class="brand-name">Nexora</span>
  <span class="brand-name">Sentivo</span>
  <span class="arrow-c"><svg width="10" height="14"><path d="M2 2l5 5-5 5" stroke="#333" stroke-width="2" fill="none"/></svg></span>
</div>

<!-- Projects -->
<h2 class="abs proj-title">Our Project</h2>
<p class="abs proj-text">With our vendor-independent expertise in best-of-breed IT infrastucture solution, not only are we to fulfill your business needs with unbiased recommendation, but we also help IT Professionals create the most cost-effective solution and best uptime that meets their ever-changing demand.</p>
<div class="proj" style="left:520px" role="img" aria-label="Bundled blue network cables in a rack"><div class="ph" style="inset:0;background:linear-gradient(180deg,#0e1a2e,#3e6fa8 45%,#23406a)"></div><h4>A Renowned China Based Listed Insurance Company</h4></div>
<div class="proj" style="left:824px" role="img" aria-label="Server cabinets in an equipment room"><div class="ph" style="inset:0;background:linear-gradient(180deg,#6c6e70,#2a2c30 50%,#3c3e42)"></div><h4>A Renown China Based Securities Firm</h4></div>
<div class="proj" style="left:1128px;width:273px" role="img" aria-label="Equipment room with cabinets"><div class="ph" style="inset:0;background:linear-gradient(180deg,#8a7a7a,#3a3438 50%,#4a4448)"></div><h4>Bay Area Property Group</h4></div>
<div class="abs arrow-c proj-next"><svg width="10" height="14"><path d="M2 2l5 5-5 5" stroke="#333" stroke-width="2" fill="none"/></svg></div>

<!-- Blogs -->
<section class="abs blogs"><h2 class="section-title">Our Blogs</h2></section>
<article class="blog" style="left:98px"><div class="ph img" role="img" aria-label="Two engineers inspecting a server rack" style="background:linear-gradient(120deg,#3d4652,#8a95a2,#2a3038)"></div><div class="meta"><svg width="14" height="14"><circle cx="7" cy="7" r="6" stroke="#222" stroke-width="1.6" fill="none"/><path d="M7 3.5V7h3" stroke="#222" stroke-width="1.6" fill="none"/></svg>Dec 19, 2023</div><h3>Lorem ipsum dolor</h3><p>Sed ut perspiciatis unde omnis iste natus error sit voluptatem accusantium doloremque laudantium, totam rem aperiam, eaque ipsa quae ab illo</p><a class="btn">Read More</a></article>
<article class="blog" style="left:441px"><div class="ph img" role="img" aria-label="Blue-lit data center aisle" style="background:radial-gradient(ellipse at 50% 60%,#4d7fd6,#1a2f6a 60%,#0a1330)"></div><div class="meta"><svg width="14" height="14"><circle cx="7" cy="7" r="6" stroke="#222" stroke-width="1.6" fill="none"/><path d="M7 3.5V7h3" stroke="#222" stroke-width="1.6" fill="none"/></svg>Dec 19, 2023</div><h3>Lorem ipsum dolor</h3><p>Sed ut perspiciatis unde omnis iste natus error sit voluptatem accusantium doloremque laudantium, totam rem aperiam, eaque ipsa quae ab illo</p><a class="btn">Read More</a></article>
<article class="blog" style="left:780px"><div class="ph img" role="img" aria-label="Data center corridor with two people" style="background:linear-gradient(180deg,#0e2030,#3a7a88 50%,#0c1a24)"></div><div class="meta"><svg width="14" height="14"><circle cx="7" cy="7" r="6" stroke="#222" stroke-width="1.6" fill="none"/><path d="M7 3.5V7h3" stroke="#222" stroke-width="1.6" fill="none"/></svg>Dec 19, 2023</div><h3>Lorem ipsum dolor</h3><p>Sed ut perspiciatis unde omnis iste natus error sit voluptatem accusantium doloremque laudantium, totam rem aperiam, eaque ipsa quae ab illo</p><a class="btn">Read More</a></article>

<!-- News -->
<h2 class="section-title news-title">News And Events</h2>
<article class="card news-big"><div class="ph img" role="img" aria-label="Glowing blue server room" style="background:radial-gradient(ellipse at 50% 55%,#5ec2ee,#1a5a9a 45%,#0a2040)"></div><div class="meta"><svg width="14" height="14"><circle cx="7" cy="7" r="6" stroke="#222" stroke-width="1.6" fill="none"/><path d="M7 3.5V7h3" stroke="#222" stroke-width="1.6" fill="none"/></svg>Dec 19, 2023</div><h3>Lorem ipsum dolor ipsum dolor</h3><p>Sed ut perspiciatis unde omnis iste natus error sit voluptatem accusantium doloremque laudantium, totam rem aperiam, eaque ipsa quae ab illo inventore veritatis et quasi architecto beatae vitae dicta sunt explicabo.&nbsp; totam rem aperiam, eaque ipsa quae ab illo inventore</p><a class="btn">Read More</a></article>
<article class="card news-small" style="top:3369px"><div class="ph img" role="img" aria-label="Engineers working at a server rack" style="background:linear-gradient(120deg,#5a6a7a,#b8c2cc,#3a4450)"></div><div class="meta"><svg width="14" height="14"><circle cx="7" cy="7" r="6" stroke="#222" stroke-width="1.6" fill="none"/><path d="M7 3.5V7h3" stroke="#222" stroke-width="1.6" fill="none"/></svg>Dec 19, 2023</div><h3>Lorem ipsum dolor ipsum dolor</h3><p>Sed ut perspiciatis unde omnis iste natus error sit voluptatem accusantium doloremque laudantium, totam rem aperiam,</p></article>
<article class="card news-small" style="top:3636px"><div class="ph img" role="img" aria-label="Technician cabling a rack" style="background:linear-gradient(120deg,#3a4a5a,#8aa0b4,#262e38)"></div><div class="meta"><svg width="14" height="14"><circle cx="7" cy="7" r="6" stroke="#222" stroke-width="1.6" fill="none"/><path d="M7 3.5V7h3" stroke="#222" stroke-width="1.6" fill="none"/></svg>Dec 19, 2023</div><h3>Lorem ipsum dolor ipsum dolor</h3><p>Sed ut perspiciatis unde omnis iste natus error sit voluptatem accusantium doloremque laudantium, totam rem aperiam,</p></article>

<!-- Contact -->
<section class="abs contact">
  <div class="ph map" role="img" aria-label="Street map of the office neighbourhood"></div>
  <h2>Contact Us</h2>
  <div class="c-row" style="top:185px"><svg width="14" height="18" viewBox="0 0 14 18"><path d="M7 1a6 6 0 0 0-6 6c0 4.5 6 10 6 10s6-5.5 6-10a6 6 0 0 0-6-6z" fill="#fff"/><circle cx="7" cy="7" r="2.2" fill="var(--navy)"/></svg><span>Rm 908, 9/F, Harbour Crest Centre, 18 Wing Lok Road, Kwun Tong, Kowloon, Hong Kong</span></div>
  <div class="c-line" style="top:263px"></div>
  <div class="c-row" style="top:294px"><svg width="18" height="14" viewBox="0 0 18 14"><rect x="1" y="1" width="16" height="12" stroke="#fff" stroke-width="1.6" fill="none"/><path d="M1 1l8 6 8-6" stroke="#fff" stroke-width="1.6" fill="none"/></svg><span>marketing@lumorasys.com.hk</span></div>
  <div class="c-line" style="top:342px"></div>
  <div class="c-row" style="top:372px"><svg width="16" height="16" viewBox="0 0 16 16"><path d="M3 1l3 3-2 2a9 9 0 0 0 6 6l2-2 3 3-2 2C7 15 1 9 1 3z" fill="#fff"/></svg><span>+852 2130 4400 / +852 5510 7788</span></div>
</section>

<!-- Footer -->
<footer class="abs footer">
  <div class="brand" style="left:98px;top:136px;font-size:38px"><span class="mark" style="width:44px;height:44px;border-width:3px"></span>Lumora</div>
  <h4 style="left:364px">USEFUL LINKS</h4>
  <ul class="flinks" style="left:364px"><li>Home</li><li>About</li><li>Our Services</li><li>Our Projects</li><li>Contact</li></ul>
  <h4 style="left:590px">HELP LINKS</h4>
  <ul class="flinks" style="left:589px"><li>Terms &amp; Conditions</li><li>Privacy Policy</li><li>About Us</li><li>Support</li></ul>
  <h4 style="left:848px">CONTACT US</h4>
  <div class="field" style="left:851px;top:103px;width:118px;height:35px">NAME</div>
  <div class="field" style="left:982px;top:103px;width:119px;height:35px">EMAIL</div>
  <div class="field" style="left:851px;top:150px;width:250px;height:35px">PHONE</div>
  <div class="field" style="left:851px;top:197px;width:250px;height:92px">MESSAGES</div>
  <a class="btn submit">Submit Now</a>
  <p class="copy">© 2023 Lumora Systems. All Rights Reserved.</p>
  <p class="legal">Compliance&nbsp; Disclaimers</p>
</footer>

</body>
</html>
```